Morlavik APP redesign and color change

I am looking for a new design for my app. Please see the attached current design.

Currently, I have a functioning app but the colors and design are awful!
The logo is great but the rest of the app needs a refresh.
(Logo hi res not yet available but will upload soon.)
New colors or anything that is cutting edge.

Basically: It is a secure social media app within a school system where the teachers, students and parents can text, exchange photos, plan curriculum, etc.

I NEED ONLY landing page with a new look!
Looking for one distinct design for the landing page with new look.
The developer will apply this one design towards the rest of the pages/app screens.

Because part of the social media I need the feel and look of what is now the trend. Something that will attract and keep the client(s) interested. I am really leaving all the creative work to the designer and open to any suggestions.

Target Market(s)

Schools, community, teachers, students, colleges, sport teams

Industry/Entity Type

Non Profit

Font styles to use
Serif
Sans Serif

Colors

Designer to choose colors to be used in the design.

Requirements
Must have
• Sharp, trendy, millennial feel
Nice to have
• Up to designer
Should not have
• Up to designer

```html
<!DOCTYPE html>
<html lang="en">
<head>
<meta charset="utf-8">
<title>Morlavik – Landing</title>
<link rel="stylesheet" href="https://fonts.googleapis.com/css2?family=Roboto:wght@400;500&family=Open+Sans:wght@400;600;700&display=swap">
<style>
  :root {
    --page-bg: #111111;
    --screen-bg: #eef0f2;
    --ink: #3a3b3d;
    --ink-dark: #1c1c1e;
    --accent-green: #4fcf8c;
    --accent-purple: #7a5cf6;
    --white: #ffffff;
  }
  * { margin: 0; padding: 0; box-sizing: border-box; }
  html, body {
    width: 1200px; height: 1200px; overflow: hidden;
    background: var(--page-bg);
    font-family: "Roboto", sans-serif;
  }
  .screen {
    position: absolute; left: 274px; top: 20px;
    width: 522px; height: 928px;
    transform: scale(1.25); transform-origin: top left;
    background: var(--screen-bg);
    overflow: hidden;
  }
  .status-bar {
    position: absolute; top: 0; left: 0; right: 0; height: 36px;
    display: flex; align-items: center; justify-content: space-between;
    padding: 0 12px; font-size: 15px; color: var(--ink-dark);
  }
  .status-left, .status-right { display: flex; align-items: center; gap: 6px; }
  .signal { letter-spacing: -1px; font-size: 11px; }
  .status-time { position: absolute; left: 0; right: 0; text-align: center; pointer-events: none; }
  .brand {
    position: absolute; top: 210px; left: 0; right: 0;
    text-align: center; color: var(--ink);
  }
  .brand-lockup {
    display: flex; align-items: center; justify-content: center; gap: 12px;
  }
  .brand-dot {
    width: 26px; height: 26px;
    border-radius: 50%; background: var(--accent-purple);
  }
  .brand-name {
    font-family: "Open Sans", sans-serif; font-weight: 600;
    font-size: 34px; letter-spacing: 0.5px; color: var(--ink);
  }
  .brand-tagline {
    margin-top: 8px;
    font-family: "Open Sans", sans-serif; font-weight: 400;
    font-size: 12px; letter-spacing: 0.6px; color: var(--ink-dark);
  }
  .photo-grid {
    position: absolute; top: 394px; left: 12px;
    display: grid; grid-template-columns: 246px 246px; grid-template-rows: 225px 225px;
    gap: 7px;
  }
  .photo { width: 100%; height: 100%; }
  .photo-students { background: linear-gradient(135deg, #e9e6e2 0%, #c9403f 45%, #3a3330 100%); }
  .photo-teacher { background: linear-gradient(160deg, #c2372e 0%, #9cbbe0 45%, #e3dcd0 100%); }
  .photo-reading { background: linear-gradient(135deg, #2f3740 0%, #8fa0a6 50%, #eef0ee 100%); }
  .photo-meeting { background: linear-gradient(150deg, #e58a1a 0%, #f3efe9 40%, #2f4fbf 100%); }
  .signup-button {
    position: absolute; left: 212px; top: 574px;
    width: 98px; height: 98px; border-radius: 50%;
    background: var(--accent-green); color: var(--white);
    font-size: 18px; font-weight: 500;
    display: flex; align-items: center; justify-content: center;
  }
  .login-bar {
    position: absolute; left: 0; right: 0; bottom: 0; height: 56px;
    background: var(--accent-purple); color: var(--white);
    display: flex; align-items: center; justify-content: space-between;
    padding: 0 12px; font-size: 16px;
  }
  .login-action { display: flex; align-items: center; gap: 14px; }
  .login-link { font-weight: 500; text-decoration: underline; }
</style>
</head>
<body>
  <main class="screen">
    <div class="status-bar">
      <div class="status-left">
        <span class="signal">●●●○○</span><span>NOVA</span>
        <svg width="16" height="12" viewBox="0 0 16 12" aria-hidden="true"><path d="M1 4a10 10 0 0 1 14 0M3.5 6.5a6.5 6.5 0 0 1 9 0M6 9a3 3 0 0 1 4 0" fill="none" stroke="currentColor" stroke-width="1.8" stroke-linecap="round"/><circle cx="8" cy="11" r="1" fill="currentColor"/></svg>
      </div>
      <div class="status-time">4:21 PM</div>
      <div class="status-right">
        <span>100%</span>
        <svg width="32" height="13" viewBox="0 0 32 13" aria-hidden="true"><rect x="0.5" y="0.5" width="28" height="12" rx="2.5" fill="none" stroke="currentColor"/><rect x="2" y="2" width="25" height="9" rx="1.5" fill="currentColor"/><rect x="30" y="4" width="1.8" height="5" rx="0.8" fill="currentColor"/></svg>
      </div>
    </div>

    <header class="brand">
      <div class="brand-lockup">
        <span class="brand-dot" aria-hidden="true"></span>
        <h1 class="brand-name">Morlavik</h1>
      </div>
      <p class="brand-tagline">SAFE SPACES FOR SCHOOL LIFE</p>
    </header>

    <section class="photo-grid">
      <div class="photo photo-students" role="img" aria-label="Group of smiling students looking at a phone together"></div>
      <div class="photo photo-teacher" role="img" aria-label="Teacher leaning over a desk helping a student in class"></div>
      <div class="photo photo-reading" role="img" aria-label="Hands holding a smartphone over a newspaper"></div>
      <div class="photo photo-meeting" role="img" aria-label="Teachers and parents talking in a classroom"></div>
    </section>

    <div class="signup-button">SIGN UP</div>

    <footer class="login-bar">
      <span>Already have an account?</span>
      <span class="login-action">
        <span><span class="login-link">LOG IN</span> now</span>
        <svg width="20" height="16" viewBox="0 0 20 16" aria-hidden="true"><path d="M1 8h17M11 1l7 7-7 7" fill="none" stroke="currentColor" stroke-width="1.8" stroke-linecap="round" stroke-linejoin="round"/></svg>
      </span>
    </footer>
  </main>
</body>
</html>
```